Stonebridge Building and Projects business cards

A business card with watermark background (construction work)

Company logo attached

Home improvement projects
House renovations
Bathroom and kitchen renovations
House extensions
New builds and granny flats

Director Omar Haddani
(Phone number)
omar@sbpbuilding.com.au
(Instagram logo) sbp_building

```html
<!DOCTYPE html>
<html lang="en">
<head>
<meta charset="utf-8">
<title>Stonebridge Building and Projects – Business Cards</title>
<link rel="stylesheet" href="https://fonts.googleapis.com/css2?family=Arimo:wght@400;700&display=swap">
<style>
  :root {
    --backdrop: #dcdcdc;
    --brand-blue: #2a6fb4;
    --card-white: #ffffff;
    --frame-dark: #1e1e22;
    --card-black: #202022;
    --silver: #c9cacc;
    --text-light: #ffffff;
  }
  * { margin: 0; padding: 0; box-sizing: border-box; }
  html, body {
    width: 1200px; height: 800px; overflow: hidden;
    background: var(--backdrop);
    font-family: "Arimo", Arial, sans-serif;
  }
  .stage { position: relative; width: 1200px; height: 800px; }
  .card {
    position: absolute; top: 245px;
    width: 520px; height: 300px;
    border-radius: 22px; overflow: hidden;
  }
  .card--front { left: 50px; background: var(--brand-blue); }
  .card--back { left: 630px; background: var(--card-black); }

  .front-panel { position: absolute; inset: 0; }

  .front-brand {
    position: absolute; left: 300px; top: 62px; width: 200px;
    display: flex; align-items: center; gap: 8px;
    color: var(--brand-blue); font-weight: 700;
  }
  .front-brand__mark { width: 14px; height: 14px; background: var(--brand-blue); flex: none; }
  .front-brand__name { font-size: 17px; line-height: 1.2; }

  .contact-block { position: absolute; left: 34px; top: 148px; color: var(--text-light); }
  .contact-block__name { font-size: 23px; font-weight: 700; letter-spacing: 0.5px; }
  .contact-block__role { font-size: 14px; margin-top: 2px; }
  .contact-list { list-style: none; margin-top: 16px; }
  .contact-list li {
    display: flex; align-items: center; gap: 8px;
    font-size: 12.5px; line-height: 19px;
  }
  .contact-list svg { width: 11px; height: 11px; flex: none; }

  .back-brand {
    position: absolute; left: 0; right: 0; top: 70px;
    text-align: center; color: var(--silver); font-weight: 700;
  }
  .back-brand__name { font-size: 34px; line-height: 1.1; }
  .back-brand__sub { font-size: 20px; line-height: 1.3; }

  .services {
    position: absolute; left: 0; right: 0; bottom: 52px;
    text-align: center; color: var(--text-light);
    font-size: 13px; line-height: 19px;
  }
</style>
</head>
<body>
<main class="stage">

  <section class="card card--front" aria-label="Business card front">
    <svg class="front-panel" viewBox="0 0 520 300" width="520" height="300" aria-hidden="true">
      <polygon points="278,0 520,0 520,168 278,226" fill="var(--frame-dark)"/>
      <polygon points="286,0 520,0 520,160 286,214" fill="var(--brand-blue)"/>
      <polygon points="290,0 520,0 520,156 290,208" fill="var(--card-white)"/>
    </svg>

    <div class="front-brand">
      <span class="front-brand__mark"></span>
      <span class="front-brand__name">Stonebridge Building and Projects</span>
    </div>

    <div class="contact-block">
      <h1 class="contact-block__name">OMAR HADDANI</h1>
      <p class="contact-block__role">Director</p>
      <ul class="contact-list">
        <li>
          <svg viewBox="0 0 24 24"><path fill="#fff" d="M6.6 10.8a15 15 0 0 0 6.6 6.6l2.2-2.2a1 1 0 0 1 1-.25 11.4 11.4 0 0 0 3.6.57 1 1 0 0 1 1 1V20a1 1 0 0 1-1 1A17 17 0 0 1 3 4a1 1 0 0 1 1-1h3.5a1 1 0 0 1 1 1c0 1.25.2 2.45.57 3.57a1 1 0 0 1-.25 1z"/></svg>
          555-304-7182
        </li>
        <li>
          <svg viewBox="0 0 24 24"><rect x="2" y="5" width="20" height="14" rx="2" fill="#fff"/><path d="M3 6l9 7 9-7" fill="none" stroke="var(--brand-blue)" stroke-width="2"/></svg>
          omar@sbpbuilding.com.au
        </li>
        <li>
          <svg viewBox="0 0 24 24"><circle cx="12" cy="12" r="10" fill="none" stroke="#fff" stroke-width="2.4"/><path d="M2 12h20M12 2c3 3 3 17 0 20M12 2c-3 3-3 17 0 20" fill="none" stroke="#fff" stroke-width="2"/></svg>
          sbpbuilding.com.au
        </li>
        <li>
          <svg viewBox="0 0 24 24"><circle cx="12" cy="12" r="10" fill="#fff"/></svg>
          sbp_building
        </li>
      </ul>
    </div>
  </section>

  <section class="card card--back" aria-label="Business card back">
    <div class="back-brand">
      <p class="back-brand__name">Stonebridge</p>
      <p class="back-brand__sub">Building and Projects</p>
    </div>
    <div class="services">
      <p>Home improvement projects :: House renovations :: House extensions</p>
      <p>Bathroom &amp; kitchen renovations :: New builds &amp; granny flats</p>
    </div>
  </section>

</main>
</body>
</html>
```